Business Card Re-Design/Update

We'd like to update out business cards. I've included our current "Style guide" which has the colour scheme of the organisation in it. I've also included the branding files with logos etc in them.

I've also included a copy of one of our existing cards so that you can see how ugly/dated they look. I'd like a fresh modern corporate look.

Target Market(s)

These are for our clients, potential clients, industry contacts - like all business cards

Contact Information for Business Card

Name
Position
Company Address - Level 1, 47 Fernby Street, Carlow Qld 4072
Direct Phone
mobile
Email
Website -www.korvalit.com.au
Logo

Colors

Designer to choose colors to be used in the design.

Requirements
Must have
• Main Logo
• Cards will need to be editable to be able to personalize them for each new employee.
Nice to have
• The MapOut, ShipWell, KeepSteady would be okay to have if they can be sensibly and professionally added to the look without detracting from the main imagery.
• Maybe they could go on the back of the card? will leave this to your creative discretion as to whether/where they fit.
Should not have
• Should not have decorative or script fonts

```html
<!DOCTYPE html>
<html lang="en">
<head>
<meta charset="utf-8">
<title>korvalIT business card</title>
<link href="https://fonts.googleapis.com/css2?family=Work+Sans:wght@400;500;600&display=swap" rel="stylesheet">
<style>
  :root {
    --red: #c8171e;
    --red-faint: #f7e3e4;
    --ink: #3a3a3c;
    --ink-soft: #555558;
    --paper: #ffffff;
    --charcoal: #2e2e30;
    --mist: #c9c9cb;
    --backdrop: #e6e6e8;
  }
  * { margin: 0; padding: 0; box-sizing: border-box; }
  html, body { width: 1200px; height: 900px; overflow: hidden; }
  body {
    background: var(--backdrop);
    font-family: "Work Sans", Arial, sans-serif;
    position: relative;
  }
  .card {
    position: absolute;
    left: 250px;
    width: 700px;
    height: 400px;
    overflow: hidden;
    box-shadow: 0 10px 30px rgba(0,0,0,0.18);
  }
  .card--front { top: 40px; background: linear-gradient(135deg, #ececec 0%, var(--paper) 45%, var(--paper) 100%); }
  .card--back { top: 470px; background: var(--charcoal); }

  .contact { position: absolute; left: 48px; top: 44px; color: var(--ink); }
  .contact__name { color: var(--red); font-weight: 600; font-size: 27px; letter-spacing: 0.5px; text-transform: uppercase; line-height: 1.1; }
  .contact__role { font-size: 15px; color: var(--ink-soft); margin-top: 4px; }
  .contact__address { font-size: 15px; line-height: 1.35; margin-top: 14px; }
  .contact__list { list-style: none; margin-top: 14px; font-size: 15px; line-height: 1.55; }
  .contact__list li { display: flex; align-items: center; gap: 10px; }
  .contact__icon { width: 12px; height: 12px; flex: none; }
  .contact__web-name { color: var(--red); }

  .brand { position: absolute; display: flex; align-items: center; gap: 12px; font-weight: 500; letter-spacing: -0.5px; }
  .brand__square { background: var(--red); flex: none; }
  .card--front .brand { right: 52px; top: 150px; font-size: 44px; color: var(--ink); }
  .card--front .brand__square { width: 38px; height: 38px; }
  .card--back .brand { left: 50%; top: 50%; transform: translate(-50%, -50%); font-size: 64px; color: var(--mist); }
  .card--back .brand__square { width: 54px; height: 54px; }

  .faint-mark { position: absolute; left: 330px; top: 245px; width: 230px; height: 230px; background: var(--red-faint); }
</style>
</head>
<body>

<section class="card card--front" aria-label="Card front">
  <div class="faint-mark" aria-hidden="true"></div>

  <div class="contact">
    <p class="contact__name">Maren Holt</p>
    <p class="contact__role">Business Development Manager</p>
    <p class="contact__address">12/58 Tallis Bridge Road,<br>Dunmore QLD 4011</p>
    <ul class="contact__list">
      <li>
        <svg class="contact__icon" viewBox="0 0 12 12"><rect x="3" y="0.5" width="6" height="11" rx="1" fill="none" stroke="#c8171e" stroke-width="1.2"/><circle cx="6" cy="9.5" r="0.7" fill="#c8171e"/></svg>
        +61 (0)400 555 182
      </li>
      <li>
        <svg class="contact__icon" viewBox="0 0 12 12"><path d="M1 5 Q6 0 11 5 L9 7 L8 5 Q6 4 4 5 L3 7 Z" fill="#c8171e"/><rect x="3" y="7.5" width="6" height="3.5" rx="1" fill="#c8171e"/></svg>
        +61 (0)7 3900 5316
      </li>
      <li>
        <svg class="contact__icon" viewBox="0 0 12 12"><path d="M2.5 1 L5 1 L5.5 3.5 L4 4.5 Q5 7 7.5 8 L8.5 6.5 L11 7 L11 9.5 Q10 11 8 10.5 Q2.5 8.5 1.5 3 Q1.5 1.5 2.5 1 Z" fill="#c8171e"/></svg>
        +61 (0)7 3900 5333
      </li>
      <li>
        <svg class="contact__icon" viewBox="0 0 12 12"><rect x="1" y="4" width="10" height="6" rx="1" fill="#c8171e"/><rect x="3" y="1" width="6" height="3" fill="none" stroke="#c8171e" stroke-width="1.2"/></svg>
        +61 (0)7 3900 5303
      </li>
      <li>
        <svg class="contact__icon" viewBox="0 0 12 12"><rect x="0.7" y="2.5" width="10.6" height="7" fill="none" stroke="#c8171e" stroke-width="1.2"/><path d="M1 3 L6 7 L11 3" fill="none" stroke="#c8171e" stroke-width="1.2"/></svg>
        mholt@korvalit.com.au
      </li>
      <li>
        <svg class="contact__icon" viewBox="0 0 12 12"><circle cx="6" cy="6" r="5.2" fill="none" stroke="#c8171e" stroke-width="1.2"/><ellipse cx="6" cy="6" rx="2.2" ry="5.2" fill="none" stroke="#c8171e" stroke-width="1"/><line x1="0.8" y1="6" x2="11.2" y2="6" stroke="#c8171e" stroke-width="1"/></svg>
        <span>www.<span class="contact__web-name">korvalit</span>.com.au</span>
      </li>
    </ul>
  </div>

  <div class="brand">
    <span class="brand__square" aria-hidden="true"></span>
    <span class="brand__name">korvalIT</span>
  </div>
</section>

<section class="card card--back" aria-label="Card back">
  <div class="brand">
    <span class="brand__square" aria-hidden="true"></span>
    <span class="brand__name">korvalIT</span>
  </div>
</section>

</body>
</html>
```